New website for a business that provides behaviour analysis

A new website that details the services that are provided around behaviour analysis for people with a disability through QPKV. There also needs to incorporate an about us and a staff page, Plus a referral form that is a google doc.
The business already has a web address that needs to be tailored.
Soft colours are preferred.
Do not have lots of pictures, keep them minimal.
A logo for the business is also needed to be incorporated, and this is a separate project that can be awarded to the website winner.
Website needs to be able to be used on WIX who will be the host for the design.

Target Market(s)

QPKV clients requiring behaviour support clician

Industry/Entity Type

Clinical behaviour support and analysis

Colors
00AB8E
00BBA5
67D7C9
C6EFE9
E9F9F6

Requirements
Must have
• Soft colours, preferable pale turquoise, minimal pictures, clean, sophisticated and classical look

```html
<!DOCTYPE html>
<html lang="en">
<head>
<meta charset="utf-8">
<title>SERENEA – Make a Referral</title>
<link href="https://fonts.googleapis.com/css2?family=Playfair+Display:wght@600;700&family=Work+Sans:wght@400;500;600&display=swap" rel="stylesheet">
<style>
:root{
  --teal:#00AB8E;
  --teal-2:#00BBA5;
  --teal-3:#67D7C9;
  --mint:#C6EFE9;
  --mint-pale:#E9F9F6;
  --ink:#1a1a1a;
  --white:#ffffff;
}
*{box-sizing:border-box;margin:0;padding:0}
html,body{width:1200px;height:2245px;overflow:hidden;background:var(--white)}
body{position:relative;font-family:"Work Sans",sans-serif;color:var(--ink)}
.abs{position:absolute}
.serif{font-family:"Playfair Display",serif;font-weight:700}
svg{display:block}

.logo{font-family:"Work Sans",sans-serif;font-weight:600;font-size:30px;letter-spacing:1px;color:var(--teal)}
.topinfo{display:flex;align-items:center;gap:8px;color:var(--teal);font-size:13.5px;line-height:18px;letter-spacing:.3px;white-space:nowrap}
.nav{left:0;top:70px;width:1200px;height:71px;background:var(--teal)}
.nav ul{position:absolute;left:165px;top:26px;display:flex;gap:19px;list-style:none;color:var(--white);font-size:15px}
.btn-appt{position:absolute;left:884px;top:15px;width:152px;height:40px;border-radius:20px;background:var(--mint-pale);color:var(--teal);font-size:13.5px;font-weight:500;display:flex;align-items:center;justify-content:center}
.hero{left:0;top:141px;width:1200px;height:213px;background:linear-gradient(90deg,#e6ece9 0%,#dcd6cd 22%,#ebeeed 45%,#f3f5f4 70%,#e5ecea 100%)}
.hero-line{left:0;top:353px;width:1200px;height:7px;background:var(--mint-pale)}
.hero-line i{position:absolute;left:269px;width:735px;height:7px;background:var(--teal)}
.hero-line b{position:absolute;left:1004px;width:196px;height:7px;background:var(--teal-2)}
.form{left:164px;top:597px;width:432px;height:390px;background:var(--teal)}
.field{position:absolute;color:var(--white);font-size:13.5px;display:flex;align-items:center;padding-left:18px;border-color:rgba(255,255,255,.9);white-space:nowrap}
.submit{position:absolute;left:0;top:346px;width:432px;height:44px;background:var(--mint-pale);color:var(--teal);font-size:13px;font-weight:500;letter-spacing:.5px;display:flex;align-items:center;justify-content:center}
.sched{left:613px;top:416px;width:423px;height:571px;background:var(--teal);color:var(--white)}
.row{position:absolute;left:44px;width:340px;display:flex;align-items:center;font-size:15px}
.row .day{width:126px}
.row .dash{width:16px;height:2px;background:var(--white);margin-right:46px}
.row .hrs{font-size:13.5px;letter-spacing:.3px}
.card{position:absolute;top:1609px;width:205px;height:204px;background:var(--mint-pale);color:var(--teal);padding:52px 0 0 26px}
.card.active{background:var(--teal);color:var(--white)}
.card h4{font-size:15px;font-weight:600;margin-top:14px;letter-spacing:.3px}
.card p{font-size:13.5px;line-height:24px;white-space:nowrap}
.footer{left:0;top:1870px;width:1200px;height:375px;background:var(--teal);color:var(--white)}
.footer h5{position:absolute;top:64px;font-size:15px;font-weight:600}
.footer ul{position:absolute;top:114px;list-style:none;font-size:13.5px;line-height:25.5px;letter-spacing:.2px}
.social{position:absolute;top:288px;width:21px;height:21px;border-radius:50%;background:var(--white)}
</style>
</head>
<body>

<div class="abs logo" style="left:165px;top:16px">SERENEA</div>
<div class="abs topinfo" style="left:490px;top:18px">
  <svg width="32" height="34" viewBox="0 0 32 34" fill="none" stroke="#00AB8E" stroke-width="1.6"><path d="M8 6l4 5-2 3c1 4 4 7 8 9l3-2 5 4-3 4C12 28 4 20 4 10z"/><path d="M17 5a10 10 0 0 1 9 9M17 10a5 5 0 0 1 4 4"/></svg>
  <div>ENQUIRIES<br>(555) 204-118-360</div>
</div>
<div class="abs topinfo" style="left:668px;top:18px">
  <svg width="30" height="30" viewBox="0 0 30 30" fill="none" stroke="#00AB8E" stroke-width="1.6"><circle cx="15" cy="15" r="13"/><path d="M15 7v8l-3 4"/></svg>
  <div>CLINIC HOURS<br>09:00 - 19:00 Mon-Sat</div>
</div>
<div class="abs topinfo" style="left:882px;top:18px">
  <svg width="30" height="34" viewBox="0 0 30 34" fill="none" stroke="#00AB8E" stroke-width="1.6"><path d="M15 32S3 20 3 13a12 12 0 0 1 24 0c0 7-12 19-12 19z"/><circle cx="15" cy="13" r="4.5"/></svg>
  <div>LOCATION<br>0123 Some Place</div>
</div>

<nav class="abs nav">
  <ul><li>Home</li><li>About us</li><li>Services</li><li>Our Staff</li><li>Resources</li><li>Contact</li></ul>
  <svg class="abs" style="left:838px;top:24px" width="22" height="22" viewBox="0 0 22 22" fill="none" stroke="#fff" stroke-width="1.8"><circle cx="9.5" cy="9.5" r="7.5"/><path d="M15 15l5 5"/></svg>
  <div class="btn-appt">Make a Referral</div>
</nav>

<div class="abs hero" role="img" aria-label="Soft-focus photo of a behaviour support clinician in a calm consulting room"></div>
<svg class="abs" style="left:0;top:141px" width="106" height="105" viewBox="0 0 106 105"><path d="M0 0h106A106 106 0 0 1 0 105z" fill="#67D7C9" opacity=".75"/></svg>
<div class="abs hero-line"><i></i><b></b></div>
<div class="abs" style="left:165px;top:209px;font-size:15px;color:var(--teal)">Home / Referral</div>
<div class="abs serif" style="left:165px;top:222px;font-size:44px;color:var(--teal)">Make a Referral</div>

<div class="abs serif" style="left:165px;top:414px;font-size:29px;font-weight:600;color:var(--teal)">Refer a Participant</div>
<p class="abs" style="left:165px;top:463px;width:420px;font-size:13.5px;line-height:19.5px">Our clinicians provide positive behaviour support and functional behaviour analysis for QPKV participants. Complete the form below and our intake team will contact you within two business days to discuss next steps.</p>

<form class="abs form">
  <div class="field" style="left:0;top:0;width:216px;height:45px;border-right:1px solid;border-bottom:1px solid">Participant Name</div>
  <div class="field" style="left:216px;top:0;width:216px;height:45px;border-bottom:1px solid">Referrer Type</div>
  <div class="field" style="left:0;top:45px;width:216px;height:45px;border-right:1px solid;border-bottom:1px solid">Email</div>
  <div class="field" style="left:216px;top:45px;width:216px;height:45px;border-bottom:1px solid">Phone</div>
  <div class="field" style="left:0;top:90px;width:216px;height:45px;border-right:1px solid;border-bottom:1px solid">Plan Type</div>
  <div class="field" style="left:216px;top:90px;width:216px;height:45px;border-bottom:1px solid">QPKV Number</div>
  <div class="field" style="left:0;top:135px;width:216px;height:45px;border-right:1px solid;border-bottom:1px solid">Clinician</div>
  <div class="field" style="left:216px;top:135px;width:216px;height:45px;border-bottom:1px solid">Service</div>
  <div class="field" style="left:0;top:180px;width:432px;height:166px;align-items:flex-start;padding-top:18px">Reason for referral</div>
  <svg class="abs" style="left:0;top:0" width="432" height="180" fill="none" stroke="#fff" stroke-width="2">
    <path d="M400 18l7 6 7-6"/><path d="M184 108l7 6 7-6"/><path d="M184 153l7 6 7-6"/><path d="M400 153l7 6 7-6"/>
  </svg>
  <div class="submit">SUBMIT REFERRAL</div>
</form>

<section class="abs sched">
  <div class="serif" style="position:absolute;left:0;top:42px;width:423px;text-align:center;font-size:42px">Clinic hours</div>
  <div class="row" style="top:146px"><span class="day">Monday</span><span class="dash"></span><span class="hrs">09:00 AM - 07:00 PM</span></div>
  <div class="row" style="top:190px"><span class="day">Tuesday</span><span class="dash"></span><span class="hrs">09:00 AM - 07:00 PM</span></div>
  <div class="row" style="top:234px"><span class="day">Wednesday</span><span class="dash"></span><span class="hrs">09:00 AM - 07:00 PM</span></div>
  <div class="row" style="top:278px"><span class="day">Thursday</span><span class="dash"></span><span class="hrs">09:00 AM - 07:00 PM</span></div>
  <div class="row" style="top:322px"><span class="day">Friday</span><span class="dash"></span><span class="hrs">09:00 AM - 07:00 PM</span></div>
  <div class="row" style="top:366px"><span class="day">Saturday</span><span class="dash"></span><span class="hrs">09:00 AM - 07:00 PM</span></div>
  <div class="row" style="top:410px"><span class="day">Sunday</span><span class="dash"></span><span class="hrs">Closed</span></div>
  <div style="position:absolute;left:66px;top:449px;width:290px;height:2px;background:var(--white)"></div>
  <svg class="abs" style="left:88px;top:487px" width="40" height="40" viewBox="0 0 32 34" fill="none" stroke="#fff" stroke-width="1.5"><path d="M8 6l4 5-2 3c1 4 4 7 8 9l3-2 5 4-3 4C12 28 4 20 4 10z"/><path d="M17 5a10 10 0 0 1 9 9M17 10a5 5 0 0 1 4 4"/></svg>
  <div style="position:absolute;left:137px;top:478px;font-size:22px;line-height:26px">Intake Line<br>(555) 204-118-360</div>
</section>

<div class="abs" style="left:164px;top:1044px;width:872px;height:394px;background:linear-gradient(100deg,#e8ebe6 0%,#e9ecea 30%,#a9d4f2 42%,#eeeae0 55%,#e6e9df 75%,#eaeae4 100%)" role="img" aria-label="Street map showing the clinic location"></div>

<div class="abs" style="left:0;top:1496px;width:1200px;text-align:center;font-size:15px;font-weight:600;letter-spacing:3.5px;color:var(--teal)">GET IN TOUCH</div>
<div class="abs serif" style="left:0;top:1518px;width:1200px;text-align:center;font-size:30px;font-weight:600;color:var(--teal)">Contact</div>

<div class="card" style="left:164px">
  <svg width="32" height="34" viewBox="0 0 32 34" fill="none" stroke="#00AB8E" stroke-width="1.6"><path d="M8 6l4 5-2 3c1 4 4 7 8 9l3-2 5 4-3 4C12 28 4 20 4 10z"/><path d="M17 5a10 10 0 0 1 9 9M17 10a5 5 0 0 1 4 4"/></svg>
  <h4>PHONE</h4><p>(555) 204-118-360<br>(555) 207-442-913</p>
</div>
<div class="card active" style="left:387px">
  <svg width="30" height="34" viewBox="0 0 30 34" fill="none" stroke="#fff" stroke-width="1.6"><path d="M15 32S3 20 3 13a12 12 0 0 1 24 0c0 7-12 19-12 19z"/><circle cx="15" cy="13" r="4.5"/></svg>
  <h4>LOCATION</h4><p>0123 Some place<br>9876 Some country</p>
</div>
<div class="card" style="left:609px">
  <svg width="34" height="34" viewBox="0 0 34 34" fill="none" stroke="#00AB8E" stroke-width="1.6"><rect x="2" y="6" width="30" height="22"/><path d="M2 6l15 12 15-12"/></svg>
  <h4>EMAIL</h4><p>hello@sereneacare.com<br><span style="font-size:12px">referrals@sereneacare.com</span></p>
</div>
<div class="card" style="left:831px">
  <svg width="30" height="34" viewBox="0 0 30 30" fill="none" stroke="#00AB8E" stroke-width="1.6"><circle cx="15" cy="15" r="13"/><path d="M15 7v8l-3 4"/></svg>
  <h4>CLINIC HOURS</h4><p>Mon-Sat 09:00-19:00<br>Sunday Closed</p>
</div>

<footer class="abs footer">
  <div class="logo" style="position:absolute;left:165px;top:58px;color:var(--white)">SERENEA</div>
  <p style="position:absolute;left:165px;top:115px;font-size:15.5px;line-height:22px">Clinical Behaviour Support<br>for Every Participant.</p>
  <h5 style="left:406px">Important Links</h5>
  <ul style="left:406px"><li>Referral</li><li>Our Staff</li><li>Services</li><li>About Us</li></ul>
  <h5 style="left:560px">Contact Us</h5>
  <ul style="left:560px"><li>Call: (555) 204-118-360</li><li>Email: hello@sereneacare.com</li><li>Address: 0123 Some place</li><li>Some country</li></ul>
  <h5 style="left:796px">Newsletter</h5>
  <div style="position:absolute;left:796px;top:115px;width:239px;height:43px;background:var(--mint-pale);border-radius:3px;color:var(--teal);font-size:13.5px;display:flex;align-items:center;padding-left:9px">Enter your email address</div>
  <svg class="abs" style="left:998px;top:126px" width="22" height="22" viewBox="0 0 22 22"><path d="M1 10L21 1 14 21l-3-8z" fill="#1f2a6b"/></svg>
  <div style="position:absolute;left:165px;top:252px;width:871px;height:1px;background:var(--mint)"></div>
  <div style="position:absolute;left:165px;top:290px;font-size:13.5px;letter-spacing:.2px">© 2021 SERENEA Behaviour Support. All Rights Reserved by BRIGHTLEAF STUDIO</div>
  <div class="social" style="left:938px"></div>
  <div class="social" style="left:977px"></div>
  <div class="social" style="left:1015px"></div>
</footer>

</body>
</html>
```